4D Cradle Glimpse Luxury Ultrasound Billboard

Design a HIGH-END, MODERN billboard for my private prenatal ultrasound studio, 4D Cradle Glimpse, located in Pace, Florida.
This billboard will be viewed by drivers traveling at highway speeds, so it must be extremely clean, simple, and readable within 6 seconds.
About My Business
4D Cradle Glimpse is a private prenatal ultrasound studio specializing in:
Highest technology 4D/HD Ultrasounds
Early Gender Determination
Pregnancy Confirmation
I have been serving families for nearly 10 years and is known for creating a memorable experience, not just an ultrasound appointment.
Design Style
I DO NOT want:
Flowers
Leaves
Swirls
Glitter
Hearts everywhere
Busy backgrounds
Generic maternity stock graphics
I DO want:
Modern
Luxury
Upscale
Clean
Professional
Eye-catching
Premium medical spa feel
Colors
Use colors from my logo:
LOGO Green ( or a deep green)
Black
White
Soft Gold accents
Images:
Incorporate my professional headshot in a clean, modern way, logo, and the ultrasound images
Text
Keep wording minimal.
Primary Headline ( OPEN TO IDEAS) :
EXAMPLES ( WOULD RATHER SOMETHING MORE CATCHY)
" ADVANCED IMAGING. UNFORGETTABLE MOMENTS"
"MEET YOUR BABY BEFORE BIRTH"
Under headline:
4D Ultrasound • Early Gender • Pregnancy Confirmation
Business Name:
4D Cradle Glimpse
Private Prenatal Ultrasound Studio
Phone Number:
850-471-5923
Important
This billboard must be readable in 5–6 seconds from a moving vehicle.
Less text is better.
The phone number and business name must be visible from a distance.
The design should feel like a premium brand that immediately tells expecting parents:
“This is where I go to see my baby.”
Files Provided
Official logo
Headshot
Ultrasound images
Don’t make this look like a medical office billboard.
Make it look like a luxury baby experience billboard. That’s what separates 4D Cradle Glimpse from hospitals, OB offices, and all the new studios popping up around you. The emotional connection is what gets moms to book. ❤️
Billboard Size - 10.6” x 36”

```html
<!DOCTYPE html>
<html lang="en">
<head>
<meta charset="utf-8">
<title>4D Cradle Glimpse Billboard</title>
<link href="https://fonts.googleapis.com/css2?family=Jost:wght@400;500;600&family=Montserrat:wght@700&display=swap" rel="stylesheet">
<style>
  :root {
    --black: #000000;
    --panel: #000000;
    --gold: #b8923f;
    --white: #ffffff;
    --frame: #d9d9d9;
    --glow: #f7d27a;
    --amber: #e0a24a;
    --copper: #c06a32;
    --umber: #6a321a;
    --sage: #6f8e72;
  }
  * { margin: 0; padding: 0; box-sizing: border-box; }
  html, body {
    width: 939px;
    height: 1200px;
    overflow: hidden;
    background: var(--black);
  }
  .billboard {
    position: absolute;
    left: 67px;
    top: 483px;
    width: 804px;
    height: 234px;
    background: var(--panel);
    border: 1px solid var(--frame);
    overflow: hidden;
  }
  .hero-photo {
    position: absolute;
    left: 0;
    top: 0;
    width: 449px;
    height: 100%;
    background:
      radial-gradient(circle at 225px 120px, var(--glow) 0%, rgba(247,210,122,0.6) 18%, rgba(247,210,122,0) 42%),
      linear-gradient(90deg, var(--sage) 0%, var(--amber) 28%, var(--amber) 45%, var(--copper) 62%, var(--umber) 84%, #2a140a 100%);
  }
  .headline {
    position: absolute;
    left: 432px;
    top: 19px;
    width: 350px;
    text-align: center;
    font-family: "Jost", sans-serif;
    font-weight: 400;
    font-size: 45px;
    line-height: 39px;
    letter-spacing: -0.5px;
    color: var(--gold);
    text-transform: uppercase;
    white-space: nowrap;
  }
  .services {
    position: absolute;
    left: 432px;
    top: 110px;
    width: 350px;
    text-align: center;
    font-family: "Jost", sans-serif;
    font-weight: 400;
    font-size: 12.5px;
    color: var(--white);
    white-space: nowrap;
  }
  .services .dot { color: var(--gold); margin: 0 3px; }
  .phone {
    position: absolute;
    left: 437px;
    top: 175px;
    font-family: "Montserrat", sans-serif;
    font-weight: 700;
    font-size: 34px;
    line-height: 40px;
    letter-spacing: -0.5px;
    color: var(--white);
    white-space: nowrap;
  }
  .brand-tile {
    position: absolute;
    left: 679px;
    top: 167px;
    width: 104px;
    height: 52px;
    background: var(--white);
    border-radius: 6px;
    display: flex;
    align-items: center;
    justify-content: center;
    text-align: center;
  }
  .brand-name {
    font-family: "Jost", sans-serif;
    font-weight: 600;
    font-size: 18px;
    line-height: 18px;
    color: var(--gold);
  }
</style>
</head>
<body>
  <section class="billboard">
    <div class="hero-photo" role="img" aria-label="Warm golden photo of a smiling mother face to face with her baby"></div>
    <h1 class="headline">Meet your baby<br>before birth</h1>
    <p class="services">4D Ultrasound<span class="dot">•</span>Early Gender<span class="dot">•</span>Pregnancy Confirmation</p>
    <p class="phone">850-471-5923</p>
    <div class="brand-tile">
      <span class="brand-name">4D Cradle<br>Glimpse</span>
    </div>
  </section>
</body>
</html>
```